University Social app needs Instagram layout help - tile layout and designs for 18 different types

We need a instagram profile look for our app Tindleloop that is getting a new look and feel. We want 18 different tiles designs that mesh well and look good together on the profile page. This can be a mix of images and text. Tindleloop is based in Sydney, Australia and is a Social app that helps students connect IRL ,find new friends and activities/experiences through society campus events. Topics can include but not limited to the following: Whats on, society spotlight, how to use Tindleloop, Tindleloop features, memes, Helpful hits, POV, Uni Life IRL, Make the Connection, Try Something New, Tindleloop Community, Student Voice, Uni 101, Tindleloop It, Student Stories. please also see current Tindleloop instagram page for content type ideas. It also needs to have the new Tindleloop brand colours (#04ccd9 with a gradient to white background) (also see attached file). The final tiles should communicate university fun, connection and a place to find events. Swap out the current stickers for activity based stickers similar to the attached examples to demonstrate that the app is for finding fun events and activities and for connection.
Look and feel
Each slider illustrates characteristics of the customer's brand and the style your logo design should communicate.

```html
<!DOCTYPE html>
<html lang="en">
<head>
<meta charset="utf-8">
<title>Student Voice – Tindleloop</title>
<link rel="stylesheet" href="https://fonts.googleapis.com/css2?family=Lexend:wght@600&family=Fredoka:wght@500&display=swap">
<style>
  :root {
    --frame: #323843;
    --brand-cyan: #04ccd9;
    --sky-blue: #00c8ff;
    --tile-top: #f4fefe;
    --tile-bottom: #6fe5ee;
    --aqua-block: #6af5f7;
    --sage-pill: #b2dcd8;
    --ink: #0b0b0b;
    --body-ink: #333a44;
    --teal-block: #4a919a;
    --leaf: #8fc497;
    --sun: #ffe100;
    --plum: #3b2370;
    --dot: #3a2a8a;
  }
  * { margin: 0; padding: 0; box-sizing: border-box; }
  html, body { width: 1200px; height: 1200px; overflow: hidden; background: var(--frame); }
  .canvas { position: relative; width: 1200px; height: 1200px; background: var(--frame); }
  .tile {
    position: absolute; left: 125px; top: 125px; width: 950px; height: 950px; overflow: hidden;
    background: linear-gradient(200deg, var(--tile-top) 0%, #ffffff 22%, #c6f5f7 55%, var(--tile-bottom) 100%);
  }
  .shape { position: absolute; }
  .aqua-block { left: 0; top: 0; width: 131px; height: 146px; background: var(--aqua-block); border-bottom-right-radius: 10px; }
  .sage-pill { left: 773px; top: 0; width: 52px; height: 135px; background: var(--sage-pill); border-radius: 0 0 26px 26px; }
  .headline {
    position: absolute; right: 161px; font-family: "Lexend", sans-serif; font-weight: 600;
    font-size: 110px; line-height: 1; color: var(--ink); letter-spacing: -1px;
  }
  .headline-top { top: 112px; }
  .headline-bottom { top: 201px; }
  .voice-blob { left: 489px; top: 203px; width: 300px; height: 108px; border-radius: 50%; background: var(--sky-blue); }
  .quote-mark { position: absolute; left: 105px; top: 291px; width: 102px; height: 74px; }
  .testimonial {
    position: absolute; left: 221px; top: 353px; width: 571px;
    font-family: "Fredoka", sans-serif; font-weight: 500; font-size: 23px; line-height: 33px; color: var(--body-ink);
  }
  .testimonial span { display: block; text-align: justify; text-align-last: justify; white-space: nowrap; }
  .testimonial .spaced { letter-spacing: 2.4px; }
  .sticker { position: absolute; }
  .sticker-heart { left: 196px; top: 132px; width: 112px; height: 100px; background: #ff5a4c; border-radius: 50% 50% 46% 46%; transform: rotate(-14deg); }
  .sticker-lol { left: 83px; top: 642px; width: 107px; height: 68px; background: #00a8f0; border-radius: 50%; transform: rotate(-24deg); }
  .sticker-planet { left: 520px; top: 795px; width: 110px; height: 124px; background: #5dd3fb; border-radius: 50%; }
  .sticker-omg { left: 695px; top: 790px; width: 185px; height: 70px; background: #ff8c1a; border-radius: 30px; transform: rotate(-28deg); }
  .dot-grid { position: absolute; left: 84px; top: 747px; width: 104px; height: 96px; }
  .half-moon { left: 224px; top: 733px; width: 65px; height: 130px; background: #ffffff; border-radius: 65px 0 0 65px; }
  .teal-block { left: 216px; top: 889px; width: 121px; height: 61px; background: var(--teal-block); border-radius: 6px 6px 0 0; }
  .leaf-dot { left: 375px; top: 773px; width: 52px; height: 52px; background: var(--leaf); border-radius: 50%; }
  .sun-pill { left: 376px; top: 840px; width: 52px; height: 120px; background: var(--sun); border-radius: 26px 26px 0 0; }
  .plum-dome { left: 757px; top: 885px; width: 129px; height: 129px; background: var(--plum); border-radius: 50%; }
</style>
</head>
<body>
<div class="canvas">
  <section class="tile">
    <div class="shape aqua-block"></div>
    <div class="shape sage-pill"></div>

    <div class="sticker sticker-heart" role="img" aria-label="Sticker of a smiling red heart character"></div>

    <div class="shape voice-blob"></div>
    <h1>
      <span class="headline headline-top">Student</span>
      <span class="headline headline-bottom">voice</span>
    </h1>

    <svg class="quote-mark" viewBox="0 0 102 74" aria-hidden="true">
      <g fill="var(--sky-blue)">
        <circle cx="24" cy="50" r="24"/>
        <path d="M2 46 C2 20 20 2 46 0 L40 16 C26 20 22 30 24 40 Z"/>
        <circle cx="78" cy="50" r="24"/>
        <path d="M56 46 C56 20 74 2 100 0 L94 16 C80 20 76 30 78 40 Z"/>
      </g>
    </svg>

    <p class="testimonial">
      <span class="spaced">Attending this academy completely</span>
      <span>transformed my career trajectory and boosted</span>
      <span>my confidence as a software developer. The</span>
      <span>hands-on projects and supportive mentors</span>
      <span>bridged the gap between theory and real-world</span>
      <span>application, allowing me to build a professional</span>
      <span class="spaced">portfolio from scratch. Thanks to the</span>
      <span class="spaced">comprehensive curriculum and dedicated</span>
      <span>career coaching, I secured my dream job as a</span>
      <span>junior engineer within two months of graduation</span>
    </p>

    <div class="sticker sticker-lol" role="img" aria-label="Blue oval sticker with playful LOL lettering"></div>

    <svg class="dot-grid" viewBox="0 0 104 96" aria-hidden="true">
      <g fill="var(--dot)">
        <circle cx="2" cy="2" r="2"/><circle cx="35" cy="2" r="2"/><circle cx="68" cy="2" r="2"/><circle cx="101" cy="2" r="2"/>
        <circle cx="2" cy="32" r="2"/><circle cx="35" cy="32" r="2"/><circle cx="68" cy="32" r="2"/><circle cx="101" cy="32" r="2"/>
        <circle cx="2" cy="63" r="2"/><circle cx="35" cy="63" r="2"/><circle cx="68" cy="63" r="2"/><circle cx="101" cy="63" r="2"/>
        <circle cx="2" cy="94" r="2"/><circle cx="35" cy="94" r="2"/><circle cx="68" cy="94" r="2"/><circle cx="101" cy="94" r="2"/>
      </g>
    </svg>

    <div class="shape half-moon"></div>
    <div class="shape teal-block"></div>
    <div class="shape leaf-dot"></div>
    <div class="shape sun-pill"></div>

    <div class="sticker sticker-planet" role="img" aria-label="Sticker of a smiling blue ringed planet character"></div>
    <div class="sticker sticker-omg" role="img" aria-label="Orange and yellow sticker with bold OMG lettering"></div>

    <div class="shape plum-dome"></div>
  </section>
</div>
</body>
</html>
```